Modern Attractive Letterhead for Veterinary House Call Business.

A letterhead which can be printed on A4, A5 and A6 paper sizes.
To have: ( our files to be uploaded)
1. Logo with Text
2. telephone
3. email
4. website
5. Address

Target Market(s)

60-85year mainly women pet owners. Also market include families, young professionals, busy people who have dogs and cats

Industry/Entity Type

Business

Requirements
Must have
• 1. Logo with Text ( provided)
• 2. telephone
• 3. email
• 4. website
• 5. Address
Nice to have
• Needs to be modern, preferably warm and caring in nature( if possible )
Should not have
• difficulty in printing A5 and A6

```html
<!DOCTYPE html>
<html lang="en">
<head>
<meta charset="utf-8">
<title>Hearthside Vet Care – Letterhead</title>
<link href="https://fonts.googleapis.com/css2?family=Cinzel:wght@400;600&display=swap" rel="stylesheet">
<style>
  :root {
    --backdrop: #ecebe8;
    --paper: #ffffff;
    --navy: #25215f;
    --brand-blue: #1f6fb3;
    --sky: #2aa8e0;
    --mid-blue: #2a6fae;
    --rule: #9a9a9a;
    --ink: #2a2a2a;
    --on-band: #ffffff;
  }
  * { box-sizing: border-box; margin: 0; padding: 0; }
  html, body {
    width: 901px;
    height: 1200px;
    overflow: hidden;
    background: var(--backdrop);
  }
  .letterhead {
    position: absolute;
    left: 50px;
    top: 36px;
    width: 796px;
    height: 1130px;
    background: var(--paper);
    box-shadow: 0 1px 4px rgba(0,0,0,0.18);
    overflow: hidden;
    font-family: "Cinzel", serif;
  }
  .brand {
    position: absolute;
    left: 26px;
    top: 62px;
    display: flex;
    align-items: center;
    gap: 12px;
  }
  .brand-dot {
    width: 38px;
    height: 38px;
    border-radius: 50%;
    background: var(--brand-blue);
  }
  .brand-name {
    font-weight: 600;
    font-size: 30px;
    color: var(--brand-blue);
    letter-spacing: 0.3px;
    white-space: nowrap;
  }
  .postal-address {
    position: absolute;
    left: 557px;
    top: 62px;
    padding-left: 10px;
    border-left: 1px solid var(--rule);
    font-size: 15px;
    line-height: 20px;
    color: var(--ink);
    font-style: normal;
  }
  .footer-band {
    position: absolute;
    left: 0;
    bottom: 0;
    width: 796px;
    height: 96px;
    background: linear-gradient(90deg, var(--sky) 0%, var(--mid-blue) 45%, var(--navy) 100%);
  }
  .contact-list {
    position: absolute;
    right: 22px;
    top: 1050px;
    list-style: none;
    color: var(--on-band);
    font-size: 13.5px;
    line-height: 22px;
    letter-spacing: 0.6px;
  }
  .contact-list li {
    display: flex;
    justify-content: flex-end;
    align-items: center;
    gap: 7px;
  }
  .contact-icon { width: 12px; height: 12px; flex: none; }
</style>
</head>
<body>
  <main class="letterhead">
    <header>
      <div class="brand">
        <span class="brand-dot"></span>
        <span class="brand-name">Hearthside Vet Care</span>
      </div>
      <address class="postal-address">
        PO Box 5520 Maplewood<br>QLD 4099
      </address>
    </header>

    <div class="footer-band" role="img" aria-label="Decorative footer wave in sky blue to navy with a green accent"></div>

    <ul class="contact-list">
      <li>
        <svg class="contact-icon" viewBox="0 0 12 12" aria-hidden="true"><circle cx="6" cy="6" r="5.3" fill="none" stroke="#fff" stroke-width="1"/><path d="M4 3.2l1 1.4-.6.7a4 4 0 0 0 2.3 2.3l.7-.6 1.4 1-.6 1a5 5 0 0 1-5.2-5.2z" fill="#fff"/></svg>
        0491570156
      </li>
      <li>
        <svg class="contact-icon" viewBox="0 0 12 12" aria-hidden="true"><rect x="1" y="3" width="10" height="7" rx="1" fill="#fff"/><path d="M1.5 3.5L6 7l4.5-3.5" fill="none" stroke="#2a4a8a" stroke-width="1"/></svg>
        info@hearthsidevet.com.au
      </li>
      <li>
        <svg class="contact-icon" viewBox="0 0 12 12" aria-hidden="true"><g fill="none" stroke="#fff" stroke-width="1"><circle cx="6" cy="6" r="5"/><ellipse cx="6" cy="6" rx="2.2" ry="5"/><path d="M1 6h10M2 3.5h8M2 8.5h8"/></g></svg>
        www.hearthsidevet.com.au
      </li>
    </ul>
  </main>
</body>
</html>
```